Photography Business, Business Card

Looking for a unique cutting edge card that takes advantage of the latest printing technologies. Please review this site for all the options they office: https://glowprintly.com. If you can think it they can do it. And if you have an idea and do not know if they can do it, I will check into it.

Target Market(s)

People and places I took images of and future clients.

Industry/Entity Type

Photography

Contact Information for Business Card

Name, cell & email. Derek Holloway, dholloway@kpnvisuals.com, 312-748-2961

Colors

Designer to choose only greyscale colors for use in the design.

Requirements
Must have
• 100% cutting edge. Is so great, those I hand it to always show it to someone else. A piece of art.
Nice to have
• Blacks, silvers, greys, some red. Maybe other colors?

```html
<!DOCTYPE html>
<html lang="en">
<head>
<meta charset="utf-8">
<title>Derek Holloway – Business Card</title>
<link rel="stylesheet" href="https://fonts.googleapis.com/css2?family=Montserrat:wght@700&family=Arimo:wght@400&display=swap">
<style>
  :root {
    --page: #ffffff;
    --card-dark: #2e2e2e;
    --tab-grey: #8e8e8e;
    --ring-grey: #9a9a9a;
    --lens-deep: #0d0d0d;
    --lens-mid: #3a3a3a;
    --text-white: #ffffff;
    --text-grey: #9b9b9b;
    --card-light: #e1e2e2;
    --frame-line: #b4b5b5;
    --logo-ink: #3c3c3c;
  }
  html, body {
    margin: 0;
    padding: 0;
    width: 1200px;
    height: 1200px;
    overflow: hidden;
    background: var(--page);
  }
  .canvas {
    display: block;
    width: 1200px;
    height: 1200px;
  }
  .card-front { fill: var(--card-dark); }
  .front-tab { fill: var(--tab-grey); }
  .lens-ring { fill: var(--ring-grey); }
  .holder-name {
    font-family: "Montserrat", sans-serif;
    font-weight: 700;
    font-size: 26px;
    fill: var(--text-white);
    letter-spacing: 0.3px;
  }
  .holder-role,
  .contact-text {
    font-family: "Arimo", sans-serif;
    font-weight: 400;
    fill: var(--text-grey);
  }
  .holder-role { font-size: 17px; }
  .contact-phone { font-size: 19px; }
  .contact-email { font-size: 17px; }
  .contact-icon {
    fill: none;
    stroke: var(--text-grey);
    stroke-width: 1.4;
    stroke-linejoin: round;
    stroke-linecap: round;
  }
  .card-back { fill: var(--card-light); }
  .back-frame {
    fill: none;
    stroke: var(--frame-line);
    stroke-width: 1.2;
  }
  .brand-name {
    font-family: "Montserrat", sans-serif;
    font-weight: 700;
    font-size: 44px;
    fill: var(--logo-ink);
    letter-spacing: 2px;
  }
</style>
</head>
<body>
<svg class="canvas" viewBox="0 0 1000 1000" xmlns="http://www.w3.org/2000/svg">
  <defs>
    <radialGradient id="lens-tone" cx="50%" cy="50%" r="50%">
      <stop offset="0%" stop-color="#1a1a1a"/>
      <stop offset="45%" stop-color="#2a2a2a"/>
      <stop offset="80%" stop-color="#3a3a3a"/>
      <stop offset="100%" stop-color="#0d0d0d"/>
    </radialGradient>
  </defs>

  <!-- Front side -->
  <g class="front">
    <path class="card-front" d="M200,101 H635 A178,178 0 0 1 635,457 H190 V111 Q190,101 200,101 Z"/>
    <path class="front-tab" d="M228,101 H288 V178 A18,18 0 0 1 270,196 H246 A18,18 0 0 1 228,178 Z"/>
    <circle class="lens-ring" cx="635" cy="280" r="178"/>
    <circle cx="635" cy="280" r="160" fill="url(#lens-tone)" role="img" aria-label="Camera lens illustration"/>

    <text class="holder-name" x="216" y="290">Derek Holloway</text>
    <text class="holder-role" x="217" y="312">Creative Visual Services</text>

    <path class="contact-icon" d="M220,347 l4,-2 l4,6 l-3,3 q2,4 6,6 l3,-3 l6,4 l-2,4 q-10,1 -16,-6 q-4,-6 -2,-12 Z"/>
    <text class="contact-text contact-phone" x="253" y="364">312-748-2961</text>

    <rect class="contact-icon" x="217" y="381" width="21" height="15" rx="1"/>
    <path class="contact-icon" d="M217,382 l10.5,8 l10.5,-8"/>
    <text class="contact-text contact-email" x="253" y="393">dholloway@kpnvisuals.com</text>
  </g>

  <!-- Back side -->
  <g class="back">
    <path class="card-back" d="M196,515 H631 A177,177 0 0 1 631,869 H186 V525 Q186,515 196,515 Z"/>
    <path class="back-frame" d="M222,537 H631 A155,155 0 0 1 631,847 H212 V547 Q212,537 222,537 Z"/>
    <text class="brand-name" x="492" y="708" text-anchor="middle">KPN Visuals</text>
  </g>
</svg>
</body>
</html>
```